Website redesign for job agency recruitment

Please refer to the attached document, “Tarvenly Work Website Brief,” for comprehensive details regarding the scope, objectives, and requirements of this website redesign project.

For imagery you can use images from this website https://www.pixelmarrowfoto.com or any other you regularly use.

Target Market(s)

Jobseekers and Companies looking for general labour

Industry/Entity Type

Services: Oil, Gas and Mining, Administrative, Construction and Trades, Warehouse and Logistics and, Manufacturing.

Number of Pages Required

5+ page

Font styles to use
Serif
Other font styles liked:
• Inter, Open-Sans or similar.

Requirements
Must have
• The requirements highlighted in the Word document attached. The final design needs to be provided in Figma including all viewports (Desktop, mobiel and tablet)
Should not have
• Website we like as a reference: www.brevicktalentco.com, www.qelvaworks.com, www.zunmarra.com, www.ferrowhires.com, www.9vtalentpool.com, www.hiringwithtrello.ca

```html
<!DOCTYPE html>
<html lang="en">
<head>
<meta charset="utf-8">
<title>Tarvenly Work — Recruitment &amp; Staffing</title>
<link href="https://fonts.googleapis.com/css2?family=Inter:wght@400;500;600;700&family=Lexend:wght@600;700;800&display=swap" rel="stylesheet">
<style>
:root{
  --navy:#15254a;
  --navy-2:#1c2d55;
  --gold:#c9a24a;
  --blue:#1d4ed8;
  --card:#f2f5f9;
  --text:#4a5568;
  --muted:#7b8494;
  --white:#ffffff;
  --line:#e6e9ee;
}
*{margin:0;padding:0;box-sizing:border-box}
html,body{width:674px;height:1200px;overflow:hidden;background:var(--white)}
body{position:relative;font-family:"Inter",sans-serif;color:var(--text)}
.abs{position:absolute}
.heading{font-family:"Lexend",sans-serif;font-weight:700;color:var(--navy)}

/* nav */
.site-nav{left:0;top:0;width:674px;height:28px;background:#eef0f3}
.brand{display:flex;align-items:center;gap:3px;font-size:6px;font-weight:700;color:var(--navy)}
.brand-dot{width:9px;height:9px;border-radius:50%;background:var(--gold)}
.nav-link{top:11px;font-size:5px;font-weight:600;letter-spacing:.3px;color:var(--navy)}
.btn-sm{height:14px;top:7px;font-size:5px;font-weight:700;display:flex;align-items:center;justify-content:center;border-radius:1.5px}
.btn-outline-dark{border:.6px solid var(--navy);color:var(--navy);background:var(--white)}
.btn-gold{background:var(--gold);color:var(--navy)}

/* hero */
.hero{left:0;top:28px;width:674px;height:372px;background:linear-gradient(90deg,#1a2547 0%,#2b3858 40%,#5b6677 75%,#6f7987 100%)}
.hero-title{left:113px;top:138px;font-family:"Lexend",sans-serif;font-weight:800;font-size:26.5px;line-height:25.5px;color:var(--white);letter-spacing:-.3px}
.hero-title .accent{color:var(--gold)}
.hero-lede{left:113px;top:223px;width:180px;padding-left:9px;border-left:1.3px solid var(--gold);font-size:7px;line-height:9.9px;color:#e7e9ef}
.hero-cta{left:113px;top:276px;width:83px;height:18px;background:var(--gold);color:var(--navy);font-size:6px;font-weight:600;display:flex;align-items:center;justify-content:center;gap:5px;box-shadow:0 3px 8px rgba(201,162,74,.35)}
.slide-bar{top:382px;height:1.3px;width:17px;background:#6b7385}
.slide-bar.active{background:var(--gold)}

/* audience cards */
.audience{top:434px;width:219px;height:164px;background:var(--card);border-radius:6px}
.audience .icon{position:absolute;left:22px;top:22px;width:22px;height:22px;border-radius:50%;background:var(--white);display:flex;align-items:center;justify-content:center}
.audience h2{position:absolute;left:22px;top:56px;font-size:13px}
.audience p{position:absolute;left:22px;top:75px;width:160px;font-size:6.4px;line-height:10.3px}
.audience .btn{position:absolute;left:22px;top:120px;height:21px;border-radius:2px;font-size:5.3px;font-weight:700;letter-spacing:.2px;display:flex;align-items:center;justify-content:center;gap:5px}
.btn-hire{width:82px;background:var(--gold);color:var(--navy)}
.btn-jobs{width:71px;background:var(--blue);color:var(--white)}

/* industries */
.eyebrow{left:0;width:674px;top:669px;text-align:center;font-size:5px;font-weight:600;letter-spacing:.3px;color:var(--gold)}
.section-title{left:0;width:674px;top:679px;text-align:center;font-size:17px}
.title-rule{left:323px;top:706px;width:28px;height:1.3px;background:var(--gold)}
.industry{top:736px;width:83px;height:158px;border-radius:4px;overflow:hidden}
.industry .caption{position:absolute;left:7px;bottom:6px}
.industry .kicker{font-size:4.2px;font-weight:700;color:var(--gold);letter-spacing:.2px}
.industry .name{font-family:"Lexend",sans-serif;font-weight:700;font-size:7px;color:var(--white);margin-top:1px}

/* cta band */
.cta-band{left:0;top:933px;width:674px;height:120px;background:var(--navy)}
.cta-box{left:112px;top:962px;width:450px;height:63px;border:.6px solid #34446a;border-radius:4px;background:var(--navy-2)}
.cta-box h3{position:absolute;left:17px;top:16px;font-family:"Lexend",sans-serif;font-weight:600;font-size:13px;color:var(--white)}
.cta-box p{position:absolute;left:17px;top:39px;font-size:6.4px;color:#aab3c6}
.cta-btn{top:21px;height:20px;font-size:5.8px;font-weight:600;display:flex;align-items:center;justify-content:center;border-radius:1.5px}
.cta-primary{left:294px;width:71px;background:var(--gold);color:var(--navy)}
.cta-secondary{left:373px;width:59px;border:.6px solid #c9cfdb;color:var(--white)}

/* footer */
.footer-blurb{left:112px;top:1093px;width:100px;font-size:4.8px;line-height:8px;color:var(--muted)}
.social{top:1125px;width:14px;height:14px;border-radius:50%;background:#f0f2f5;display:flex;align-items:center;justify-content:center}
.footer-col h4{font-size:5.6px;font-weight:700;color:var(--navy);margin-bottom:8px}
.footer-col a{display:block;font-size:4.8px;color:var(--muted);text-decoration:none;margin-bottom:7.6px}
.footer-address{font-size:4.8px;line-height:8px;color:var(--muted)}
.footer-phone{font-size:4.8px;color:var(--muted);margin-top:8px}
.footer-phone b{color:var(--navy)}
.footer-rule{left:112px;top:1155px;width:450px;height:.5px;background:var(--line)}
.copyright{left:0;width:674px;top:1167px;text-align:center;font-size:4px;color:#a2a9b6}
.legal{left:0;width:674px;top:1179px;text-align:center;font-size:4px;color:#a2a9b6;word-spacing:0}
.legal span{margin:0 4px}
</style>
</head>
<body>

<header class="abs site-nav">
  <div class="abs brand" style="left:122px;top:9px"><span class="brand-dot"></span>Tarvenly Work</div>
  <span class="abs nav-link" style="left:240px">FOR CANDIDATES</span>
  <span class="abs nav-link" style="left:300px">FOR EMPLOYERS</span>
  <span class="abs nav-link" style="left:358px">INDUSTRIES</span>
  <span class="abs nav-link" style="left:404px">ABOUT US</span>
  <span class="abs btn-sm btn-outline-dark" style="left:482px;width:31px">Sign In</span>
  <span class="abs btn-sm btn-gold" style="left:519px;width:34px">Register</span>
</header>

<section class="abs hero" role="img" aria-label="Dusk view of a Canadian city skyline with high-rise towers"></section>
<h1 class="abs hero-title">Connecting Talent<br><span class="accent">with Opportunity</span><br>Across Canada</h1>
<p class="abs hero-lede">Empowering industry leaders and top-tier professionals with specialized recruitment and staffing solutions throughout the Canadian landscape.</p>
<span class="abs hero-cta">Contact Us
  <svg width="5" height="5" viewBox="0 0 10 10"><path d="M1 5h8M5.5 1.5 9 5l-3.5 3.5" fill="none" stroke="currentColor" stroke-width="1.4"/></svg></span>
<span class="abs slide-bar active" style="left:113px"></span>
<span class="abs slide-bar" style="left:132px"></span>
<span class="abs slide-bar" style="left:152px"></span>
<svg class="abs" style="left:179px;top:379px" width="6" height="7" viewBox="0 0 6 8"><path d="M4.5 1 1.5 4l3 3" fill="none" stroke="#c9cdd6" stroke-width="1"/></svg>
<svg class="abs" style="left:195px;top:379px" width="6" height="7" viewBox="0 0 6 8"><path d="M1.5 1l3 3-3 3" fill="none" stroke="#c9cdd6" stroke-width="1"/></svg>

<article class="abs audience" style="left:112px">
  <span class="icon"><svg width="10" height="9" viewBox="0 0 10 9"><rect x="1" y="1" width="5" height="7" fill="none" stroke="#c9a24a" stroke-width=".8"/><rect x="6" y="3" width="3" height="5" fill="none" stroke="#c9a24a" stroke-width=".8"/><path d="M2.5 3h2M2.5 5h2" stroke="#c9a24a" stroke-width=".7"/></svg></span>
  <h2 class="heading">For Employers</h2>
  <p>Access top-tier Canadian talent across specialized sectors. Our strategic recruitment process ensures the perfect match for your corporate vision.</p>
  <span class="btn btn-hire">HIRING SOLUTIONS
    <svg width="5" height="5" viewBox="0 0 10 10"><path d="M1 5h8M5.5 1.5 9 5l-3.5 3.5" fill="none" stroke="currentColor" stroke-width="1.4"/></svg></span>
</article>

<article class="abs audience" style="left:343px">
  <span class="icon"><svg width="10" height="10" viewBox="0 0 10 10"><circle cx="4" cy="3" r="1.8" fill="none" stroke="#1d4ed8" stroke-width=".8"/><path d="M1 8.5c0-2 1.5-3 3-3" fill="none" stroke="#1d4ed8" stroke-width=".8"/><circle cx="6.8" cy="6.8" r="1.5" fill="none" stroke="#1d4ed8" stroke-width=".8"/><path d="M7.9 7.9 9.2 9.2" stroke="#1d4ed8" stroke-width=".8"/></svg></span>
  <h2 class="heading">For Candidates</h2>
  <p>Take the next step in your professional journey. Explore premium opportunities with Canada's leading organizations across diverse industries.</p>
  <span class="btn btn-jobs">BROWSE JOBS
    <svg width="5" height="5" viewBox="0 0 10 10"><path d="M1 5h8M5.5 1.5 9 5l-3.5 3.5" fill="none" stroke="currentColor" stroke-width="1.4"/></svg></span>
</article>

<p class="abs eyebrow">SPECIALIZED SECTORS</p>
<h2 class="abs heading section-title">Industries We Serve</h2>
<span class="abs title-rule"></span>

<div class="abs industry" style="left:112px;background:linear-gradient(180deg,#3d4656 0%,#5a4a44 50%,#9a6a3a 72%,#1d2533 100%)" role="img" aria-label="Offshore oil platform at sunset">
  <div class="caption"><div class="kicker">ENERGY</div><div class="name">OIL &amp; GAS</div></div>
</div>
<div class="abs industry" style="left:204px;background:linear-gradient(180deg,#111418 0%,#2a3038 45%,#5a5d62 70%,#1b1e24 100%)" role="img" aria-label="Office desk with a computer monitor and keyboard">
  <div class="caption"><div class="kicker">CORPORATE</div><div class="name">ADMIN</div></div>
</div>
<div class="abs industry" style="left:295px;background:linear-gradient(180deg,#6f8a55 0%,#3f5a3a 35%,#24392e 60%,#4a4a46 100%)" role="img" aria-label="Construction site fence beneath trees">
  <div class="caption"><div class="kicker">INFRASTRUCTURE</div><div class="name">CONSTRUCTION</div></div>
</div>
<div class="abs industry" style="left:387px;background:linear-gradient(180deg,#6a7480 0%,#8a929c 35%,#3e4f6d 65%,#2a3650 100%)" role="img" aria-label="Warehouse aisle lined with tall storage racks">
  <div class="caption"><div class="kicker">LOGISTICS</div><div class="name">WAREHOUSE</div></div>
</div>
<div class="abs industry" style="left:478px;background:linear-gradient(180deg,#7c8a84 0%,#4f7d88 40%,#9a7650 70%,#2c3a4a 100%)" role="img" aria-label="Factory worker packing boxes on a production line">
  <div class="caption"><div class="kicker">INDUSTRIAL</div><div class="name">MANUFACTURING</div></div>
</div>

<section class="abs cta-band"></section>
<div class="abs cta-box">
  <h3>Ready to start your journey?</h3>
  <p>Join thousands of professionals finding their next career move with Tarvenly Work.</p>
  <span class="abs cta-btn cta-primary">Submit Resume</span>
  <span class="abs cta-btn cta-secondary">Contact Us</span>
</div>

<footer>
  <div class="abs brand" style="left:115px;top:1069px"><span class="brand-dot"></span>Tarvenly Work</div>
  <p class="abs footer-blurb">Canada's premier partner in specialized recruitment and staffing solutions across energy, admin, and construction sectors.</p>
  <span class="abs social" style="left:112px"><svg width="6" height="6" viewBox="0 0 10 10"><circle cx="7.5" cy="2" r="1.3" fill="#4a5568"/><circle cx="2.5" cy="5" r="1.3" fill="#4a5568"/><circle cx="7.5" cy="8" r="1.3" fill="#4a5568"/><path d="M7.5 2 2.5 5l5 3" fill="none" stroke="#4a5568" stroke-width=".8"/></svg></span>
  <span class="abs social" style="left:132px"><svg width="6" height="5" viewBox="0 0 10 8"><rect x=".5" y=".5" width="9" height="7" fill="none" stroke="#4a5568" stroke-width=".9"/><path d="M.5 .5 5 4.5 9.5.5" fill="none" stroke="#4a5568" stroke-width=".9"/></svg></span>
  <span class="abs social" style="left:152px"><svg width="6" height="6" viewBox="0 0 10 10"><path d="M2 1h2l1 2.5-1.3 1a6 6 0 0 0 2.8 2.8l1-1.3L10 7v2a1 1 0 0 1-1 1A8.5 8.5 0 0 1 1 2a1 1 0 0 1 1-1z" fill="none" stroke="#4a5568" stroke-width=".8"/></svg></span>

  <nav class="abs footer-col" style="left:229px;top:1075px">
    <h4>Quick Links</h4>
    <a>Find a Job</a><a>Post a Job</a><a>Talent Solutions</a><a>Career Advice</a>
  </nav>
  <nav class="abs footer-col" style="left:345px;top:1075px">
    <h4>Industries</h4>
    <a>Energy &amp; Resources</a><a>Corporate Admin</a><a>Construction &amp; Trades</a><a>Supply Chain</a>
  </nav>
  <div class="abs footer-col" style="left:462px;top:1075px">
    <h4>Headquarters</h4>
    <p class="footer-address">48 Harbourline Ave, 9th Floor<br>Toronto, ON M4A 1B2<br>Canada</p>
    <p class="footer-phone"><b>Toll-Free:</b> 1-800-555-0147</p>
  </div>
  <span class="abs footer-rule"></span>
  <p class="abs copyright">© 2024 Tarvenly Work Recruitment &amp; Staffing. All rights reserved.</p>
  <p class="abs legal"><span>Privacy Policy</span><span>Terms of Service</span><span>Accessibility</span></p>
</footer>

</body>
</html>
```